Business card design needed

I would like a one sided black business card with the information provided above. Refer to my website www.brightvolleyracquets.com.au for an example of colors I have used for my site, would like to keep this consistent for my business cards also, I will upload my logo below.

I am a new small business that provides tennis customers with racquet re stringing, tennis strings and accessories.

Industry/Entity Type

Small Business

Contact Information for Business Card

Bright Volley Tennis

Owen Whitby
Managing Director

brightvolleyracquets@mailbox.example
www.brightvolleyracquets.com.au
0491 726 305

Racquet Restringing/Tennis Strings/Accessories

Requirements
Must have
• Must have my logo and card must be black

```html
<!DOCTYPE html>
<html lang="en">
<head>
<meta charset="utf-8">
<title>Bright Volley Tennis – Business Card</title>
<link rel="stylesheet" href="https://fonts.googleapis.com/css2?family=Open+Sans:ital,wght@0,400;0,600;0,700;1,700&display=swap">
<style>
  :root {
    --backdrop: #e9e6e1;
    --card-black: #050505;
    --lime: #c2d94c;
    --blue-deep: #3c5fa6;
    --blue-soft: #7090d4;
    --white: #ffffff;
    --ink: #141414;
  }
  * { margin: 0; padding: 0; box-sizing: border-box; }
  html, body {
    width: 1200px;
    height: 750px;
    overflow: hidden;
    background: var(--backdrop);
    font-family: "Open Sans", Arial, sans-serif;
  }
  .card {
    position: absolute;
    left: 75px;
    top: 75px;
    width: 1050px;
    height: 600px;
    border-radius: 40px;
    overflow: hidden;
    background: var(--card-black);
  }
  .card__waves {
    position: absolute;
    inset: 0;
    width: 1050px;
    height: 600px;
  }
  .brand {
    position: absolute;
    left: 72px;
    top: 150px;
    display: flex;
    align-items: center;
    gap: 18px;
  }
  .brand__dot {
    width: 40px;
    height: 40px;
    border-radius: 50%;
    background: var(--lime);
  }
  .brand__name {
    color: var(--lime);
    font-weight: 700;
    font-size: 46px;
    letter-spacing: 0.5px;
    white-space: nowrap;
  }
  .contact-person {
    position: absolute;
    right: 50px;
    top: 143px;
    text-align: right;
    color: var(--white);
  }
  .contact-person__name {
    color: var(--lime);
    font-weight: 700;
    font-size: 32px;
    line-height: 44px;
  }
  .contact-person__role {
    font-size: 25px;
    line-height: 36px;
  }
  .contact-person__phone {
    font-size: 25px;
    line-height: 36px;
    margin-top: 10px;
    margin-right: 7px;
  }
  .label {
    font-weight: 700;
    font-style: italic;
    margin-right: 6px;
  }
  .services {
    position: absolute;
    left: 68px;
    top: 343px;
    list-style: none;
    color: var(--white);
    font-size: 28px;
    line-height: 40px;
  }
  .services li::before {
    content: "";
    display: inline-block;
    width: 10px;
    height: 10px;
    background: var(--white);
    margin-right: 10px;
    vertical-align: 6px;
  }
  .contact-web {
    position: absolute;
    right: 20px;
    top: 506px;
    text-align: right;
    color: var(--ink);
    font-size: 24px;
    line-height: 34px;
  }
</style>
</head>
<body>
  <section class="card">
    <svg class="card__waves" viewBox="0 0 1050 600" aria-hidden="true">
      <path fill="var(--blue-deep)" d="M0,452 C200,520 480,500 730,445 C500,500 220,540 0,498 Z"/>
      <path fill="var(--blue-soft)" d="M0,505 C280,560 640,480 990,425 C680,490 300,590 0,540 Z"/>
      <path fill="var(--lime)" d="M0,562 C320,560 660,470 1050,412 L1050,600 L0,600 Z"/>
    </svg>

    <div class="brand">
      <span class="brand__dot"></span>
      <span class="brand__name">Bright Volley Tennis</span>
    </div>

    <div class="contact-person">
      <p class="contact-person__name">Owen Whitby</p>
      <p class="contact-person__role">Managing Director</p>
      <p class="contact-person__phone"><span class="label">p</span>0491 726 305</p>
    </div>

    <ul class="services">
      <li>Racquet Restringing</li>
      <li>Tennis Strings</li>
      <li>Accessories</li>
    </ul>

    <div class="contact-web">
      <p><span class="label">e</span>brightvolleyracquets@mailbox.example</p>
      <p><span class="label">w</span>www.brightvolleyracquets.com.au</p>
    </div>
  </section>
</body>
</html>
```